Direct to Consumer extended service contract business with a new disruptive business model needs a

We need a customized wordpress design for a company called 'Bright Harbor Assurance'.
We provide an innovative and unique service contract protection program direct to consumers. This program provides monthly coverage for all electronics purchased in the last 4 years and all electronics the consumer purchases in the future for a low monthly fee. The overall design should communicate a sense of legitimacy, ethics, and superior customer service and support (in an industry that has a huge PR issue to overcome).
Electronics is the first product group, other product groups with different price points to launch in the future..

Target Market(s)

All purchasers of electronic goods...all demographics

Industry/Entity Type

Electronics

Font styles to use
Sans Serif

Requirements
Must have
• Customer Testimonials
Industry News
Customer ratings
Blog posts
Call to action messaging
Like the functional elements and design of quillmesa.example (need to be better)
Nice to have
• Like to see video testimonials
Social network "whats trending related to electronics or service contract industry"
Easy way to register products for warranty

```html
<!DOCTYPE html>
<html lang="en">
<head>
<meta charset="utf-8">
<title>Bright Harbor Assurance</title>
<link href="https://fonts.googleapis.com/css2?family=Open+Sans:wght@400;600;700;800&display=swap" rel="stylesheet">
<style>
:root{
  --green:#3f8f2c;
  --green-dark:#2f6e20;
  --green-light:#6cc04a;
  --charcoal:#3d3d3d;
  --charcoal-dark:#2b2b2b;
  --band:#555a5e;
  --page:#eeeeee;
  --panel:#ffffff;
  --text:#444;
  --muted:#888;
  --rule:#d6d6d6;
  --star:#e8892b;
  --red:#c8342a;
}
*{box-sizing:border-box;margin:0;padding:0}
html,body{width:798px;height:1200px;overflow:hidden}
body{font-family:"Open Sans",Arial,sans-serif;color:var(--text);background:var(--page);font-size:9px;line-height:1.4;position:relative}
.wrap{width:730px;margin:0 auto;position:relative}

/* header */
.site-header{background:var(--panel);height:54px}
.site-header .wrap{height:54px}
.brand{position:absolute;left:0;top:9px;display:flex;align-items:center;gap:6px;color:var(--green);font-weight:800;font-size:15px;letter-spacing:.5px;text-transform:uppercase;line-height:1}
.brand-mark{width:12px;height:12px;background:var(--green)}
.contact{position:absolute;right:0;top:5px;display:flex;gap:14px;font-size:8px;color:var(--charcoal);align-items:center}
.contact span{display:flex;align-items:center;gap:3px}
.login{background:var(--green);color:#fff;padding:2px 10px;font-weight:600}
.main-nav{position:absolute;right:0;top:24px;display:flex;background:var(--charcoal)}
.main-nav a{color:#fff;text-decoration:none;font-size:8px;font-weight:700;padding:7px 13px;border-left:1px solid #555}
.main-nav a.active{background:var(--charcoal-dark)}

/* hero */
.hero{height:320px;background:linear-gradient(180deg,#fafafa,#e4e4e4);position:relative}
.hero .wrap{height:320px}
.hero-copy{position:absolute;left:30px;top:130px;width:270px}
.hero-copy h1{color:var(--green);font-size:17px;font-weight:800;line-height:1.25;text-transform:uppercase}
.hero-copy p{font-size:9px;color:var(--muted);margin-top:6px}
.solution{margin-top:14px;background:#fff;border:1px solid var(--rule);width:150px;padding:6px 8px}
.solution strong{color:var(--red);font-size:8px;display:block;text-transform:uppercase}
.solution span{color:var(--green);font-size:9px}
.hero-visual{position:absolute;right:20px;top:22px;width:400px;height:270px;background:radial-gradient(ellipse at 50% 45%,#9aa3aa,#c9cfd3 55%,#e6e6e6 80%);border-radius:6px}
.arrow{position:absolute;top:150px}
.arrow.left{left:-24px}.arrow.right{right:-24px}
.dots{position:absolute;left:30px;top:300px;display:flex;gap:4px}
.dots i{width:7px;height:7px;border-radius:50%;background:#bbb}
.dots i:first-child{background:var(--charcoal)}

/* features band */
.features{background:var(--band);padding:16px 0;height:140px}
.features .wrap{display:flex;gap:10px}
.feature{flex:1;height:108px;position:relative;overflow:hidden}
.feature .shot{position:absolute;inset:0}
.f1 .shot{background:linear-gradient(135deg,#1c3a66,#3f78b5)}
.f2 .shot{background:linear-gradient(135deg,#0f2a4a,#2d8bc4)}
.f3 .shot{background:linear-gradient(135deg,#c9c9c9,#8c8c8c)}
.feature h3{position:absolute;left:0;right:0;bottom:0;background:rgba(0,0,0,.55);color:#fff;font-size:8px;font-weight:700;padding:5px 8px;text-transform:uppercase}

/* blog + testimonials */
.content{padding:20px 0 0}
.row{display:flex;gap:14px}
.card{background:var(--panel);flex:1;padding:8px 10px;position:relative}
.blog-row .card{height:196px}
.card-title{font-size:8px;font-weight:800;color:var(--green);text-transform:uppercase;border-bottom:1px solid var(--rule);padding-bottom:5px;margin-bottom:8px}
.pager{position:absolute;right:10px;top:7px;color:#999;font-size:9px;letter-spacing:4px}
.blog-body{display:flex;gap:10px}
.blog-thumb{width:110px;height:95px;background:linear-gradient(135deg,#2f8a2a,#9ad34f);flex:none}
.blog-body h4{font-size:9px;font-weight:700;color:var(--charcoal);line-height:1.3}
.blog-body p{font-size:7.5px;color:var(--muted);margin-top:4px}
.btn{display:inline-block;background:var(--green-dark);color:#fff;font-size:7px;font-weight:700;padding:3px 8px;text-transform:uppercase;margin-top:6px}
.video{height:155px;background:linear-gradient(135deg,#b8aa95,#7e7466);position:relative}
.play{position:absolute;left:50%;top:50%;transform:translate(-50%,-50%)}

/* ratings */
.ratings{margin-top:16px;background:var(--panel);padding:8px 10px 12px}
.rating-grid{display:flex}
.rating{flex:1;text-align:center}
.stars{display:flex;justify-content:center;gap:2px}
.rating h5{font-size:10px;font-weight:700;color:var(--charcoal);margin-top:4px}
.rating p{font-size:7px;color:var(--muted)}
.rating .btn{background:#666;margin-top:3px}

/* news + posts */
.news-row{margin-top:20px}
.news-row .card{height:232px}
.news-list li{list-style:none;display:flex;gap:6px;font-size:7.5px;color:var(--muted);padding:6px 0;border-bottom:1px solid #eee}
.news-list li b{color:var(--green)}
.view-more{position:absolute;right:10px;top:7px;font-size:7px;font-weight:700;color:var(--charcoal)}
.post{display:flex;gap:6px;padding:6px 0;border-bottom:1px solid #eee}
.post-mark{width:14px;height:14px;background:var(--green);flex:none}
.post p{font-size:7.5px;color:var(--text)}
.post time{font-size:6.5px;color:var(--muted)}
.feed-head{display:flex;align-items:center;gap:5px;font-size:8px;font-weight:700;color:var(--charcoal);margin-bottom:3px}
.news-more{position:absolute;right:10px;bottom:12px}

/* footer */
.site-footer{position:absolute;left:0;right:0;top:1140px;height:60px;background:var(--charcoal-dark);color:#bbb;font-size:7px}
.site-footer .wrap{padding-top:12px}
.follow{display:flex;align-items:center;gap:4px}
.follow i{width:11px;height:11px;background:#666;display:inline-block}
.footer-links{position:absolute;right:0;top:12px;text-align:right}
.footer-links nav{display:flex;gap:8px;justify-content:flex-end}
.footer-links p{margin-top:4px}
</style>
</head>
<body>
<header class="site-header">
  <div class="wrap">
    <div class="brand"><span class="brand-mark"></span>Bright Harbor Assurance</div>
    <div class="contact">
      <span><svg width="8" height="8" viewBox="0 0 10 10"><path d="M2 0h2l1 3-1.5 1a6 6 0 0 0 2.5 2.5L7 5l3 1v2c0 1-1 2-2 2A8 8 0 0 1 0 2c0-1 1-2 2-2z" fill="#3f8f2c"/></svg>855-500-HARBOR (4272)</span>
      <span><svg width="8" height="8" viewBox="0 0 10 10"><circle cx="5" cy="5" r="4" fill="none" stroke="#3f8f2c" stroke-width="1.5"/></svg>Support</span>
      <span class="login">Login</span>
    </div>
    <nav class="main-nav">
      <a class="active">HOME</a><a>PLANS</a><a>BENEFITS</a><a>FAQ</a><a>ABOUT US</a>
    </nav>
  </div>
</header>

<section class="hero">
  <div class="wrap">
    <div class="hero-visual" role="img" aria-label="Laptop on a desk with a hand resting beside it"></div>
    <svg class="arrow left" width="12" height="20" viewBox="0 0 12 20"><path d="M10 2 2 10l8 8" fill="none" stroke="#aaa" stroke-width="2"/></svg>
    <svg class="arrow right" width="12" height="20" viewBox="0 0 12 20"><path d="m2 2 8 8-8 8" fill="none" stroke="#aaa" stroke-width="2"/></svg>
    <div class="hero-copy">
      <h1>The days of buying expensive in store service plans are over!</h1>
      <p>Dont buy anymore IN store service plans</p>
      <div class="solution"><strong>Bright Harbor Assurance</strong><span>is the solution</span></div>
    </div>
    <div class="dots"><i></i><i></i><i></i></div>
  </div>
</section>

<section class="features">
  <div class="wrap">
    <div class="feature f1"><div class="shot" role="img" aria-label="Blue circuit board close-up"></div><h3>Superior Coverage</h3></div>
    <div class="feature f2"><div class="shot" role="img" aria-label="Glowing blue network lines"></div><h3>Revolutionary Protection</h3></div>
    <div class="feature f3"><div class="shot" role="img" aria-label="Customer service agent with a headset"></div><h3>Hassle Free Customer Service</h3></div>
  </div>
</section>

<main class="content">
  <div class="wrap">
    <div class="row blog-row">
      <article class="card">
        <h2 class="card-title">Our Blog</h2><span class="pager">‹›</span>
        <div class="blog-body">
          <div class="blog-thumb" role="img" aria-label="Green circuit board"></div>
          <div>
            <h4>Lorem ipsum is simply dummy text of the printing and typesetting industry. Lorem</h4>
            <p>Contrary to popular belief, coverage is not simply random text. It has roots in a plain classical idea from over two thousand years old. A professor looked up one of the more obscure words and found the source.</p>
            <span class="btn">Read More</span>
          </div>
        </div>
      </article>
      <article class="card">
        <h2 class="card-title">Customer Testimonials</h2><span class="pager">‹›</span>
        <div class="video" role="img" aria-label="Video testimonial of a group of smiling customers">
          <svg class="play" width="30" height="30" viewBox="0 0 30 30"><circle cx="15" cy="15" r="13" fill="rgba(0,0,0,.35)" stroke="#fff" stroke-width="2"/><path d="M12 9v12l9-6z" fill="#fff"/></svg>
        </div>
      </article>
    </div>

    <section class="ratings">
      <h2 class="card-title">Customer Ratings</h2>
      <div class="rating-grid">
        <div class="rating">
          <div class="stars"><svg width="70" height="13" viewBox="0 0 70 13"><g fill="#e8892b"><path id="s" d="M6.5 0 8.4 4.3 13 4.7 9.5 7.7 10.5 12.3 6.5 9.9 2.5 12.3 3.5 7.7 0 4.7 4.6 4.3z"/><use href="#s" x="14"/><use href="#s" x="28"/><use href="#s" x="42"/></g><use href="#s" x="56" fill="#ccc"/></svg></div>
          <h5>Orchard App Shelf</h5><p>4.5 average on 7000+ reviews</p><span class="btn">Read Reviews</span>
        </div>
        <div class="rating">
          <div class="stars"><svg width="70" height="13" viewBox="0 0 70 13"><g fill="#e8892b"><use href="#s"/><use href="#s" x="14"/><use href="#s" x="28"/><use href="#s" x="42"/></g><use href="#s" x="56" fill="#ccc"/></svg></div>
          <h5>Riverline</h5><p>4.5 average on 7000+ reviews</p><span class="btn">Read Reviews</span>
        </div>
        <div class="rating">
          <div class="stars"><svg width="70" height="13" viewBox="0 0 70 13"><g fill="#e8892b"><use href="#s"/><use href="#s" x="14"/><use href="#s" x="28"/><use href="#s" x="42"/></g><use href="#s" x="56" fill="#ccc"/></svg></div>
          <h5>Searchly</h5><p>4.5 average on 7000+ reviews</p><span class="btn">Read Reviews</span>
        </div>
        <div class="rating">
          <div class="stars"><svg width="70" height="13" viewBox="0 0 70 13"><g fill="#e8892b"><use href="#s"/><use href="#s" x="14"/><use href="#s" x="28"/><use href="#s" x="42"/></g><use href="#s" x="56" fill="#ccc"/></svg></div>
          <h5>Searchly+</h5><p>4.5 average on 7000+ reviews</p><span class="btn">Read Reviews</span>
        </div>
      </div>
    </section>

    <div class="row news-row">
      <section class="card">
        <h2 class="card-title">News</h2>
        <ul class="news-list">
          <li><b>›</b>Lorem ipsum is simply dummy text of the printing and typesetting industry.</li>
          <li><b>›</b>Many plans fail at the counter when customers need them most, a new study shows.</li>
          <li><b>›</b>The standard chunk of text used since the 1500s is reproduced below for those interested.</li>
          <li><b>›</b>There are many variations of passages available, but most have been changed.</li>
        </ul>
        <span class="btn news-more">Read More News</span>
      </section>
      <section class="card">
        <h2 class="card-title">Latest Posts</h2><span class="view-more">VIEW MORE ›</span>
        <div class="feed-head"><span class="post-mark"></span>Bright Harbor Assurance</div>
        <div class="post"><span class="post-mark"></span><div><p>Lorem ipsum is simply dummy text of the printing industry.</p><time>20 August 2014</time></div></div>
        <div class="post"><span class="post-mark"></span><div><p>Lorem ipsum is simply dummy text of the printing industry.</p><time>20 August 2014</time></div></div>
        <div class="post"><span class="post-mark"></span><div><p>Lorem ipsum is simply dummy text of the printing industry.</p><time>20 August 2014</time></div></div>
        <div class="post"><span class="post-mark"></span><div><p>Lorem ipsum is simply dummy text of the printing industry.</p><time>20 August 2014</time></div></div>
      </section>
    </div>
  </div>
</main>

<footer class="site-footer">
  <div class="wrap">
    <div class="follow">FOLLOW US ON <i></i><i></i><i></i></div>
    <div class="footer-links">
      <nav><span>Plans</span><span>Benefits</span><span>FAQs</span><span>About Us</span><span>Support</span><span>Privacy Policy</span><span>Terms &amp; Conditions</span><span>Contact Us</span></nav>
      <p>© 2014 Bright Harbor Assurance. All Rights Reserved.</p>
    </div>
  </div>
</footer>
</body>
</html>
```